Business card design Needed for new logo / Construction business, home extensions and new builds

We need a business card design using our new logo files which i will attach to this project :)

We are a small construction business specialising in home extensions, new builds and property development. We are very ambitious and would appreciate professional and elegant designs for our new business card.

Very serious about using the services on MakerQuarry and recently acquired our new logo from here :)

Please get involved, i will feedback when i can as i am very busy but can respond daily, thanks

Target Market(s)

People that want to build onto their houses, new building developments or adding too their existing property

Industry/Entity Type

Construction

Contact Information for Business Card

Renwick Tolliver Construction, Lionel Ashby (Managing Director), Tel 07822254961, email - info@renwick-tolliver, www.renwick-tolliver.co.uk

Colors

Designer to choose colors to be used in the design.

Requirements
Must have
• I like a deep grey on the back please. A lot of you have provided black from and back, try mixing things up a little. The black looks cool 😎 Thanks

```html
<!DOCTYPE html>
<html lang="en">
<head>
<meta charset="utf-8">
<title>Renwick Tolliver Construction – Business Card</title>
<link rel="stylesheet" href="https://fonts.googleapis.com/css2?family=Montserrat:wght@400;500;700;800&display=swap">
<style>
  :root {
    --page: #ececec;
    --card-front: #1c1c1c;
    --card-back: #262626;
    --texture-light: #2c2c2c;
    --texture-dark: #151515;
    --gold: #e0b324;
    --gold-deep: #c9971a;
    --silver: #c9c9c9;
    --ink: #141414;
  }
  * { box-sizing: border-box; margin: 0; padding: 0; }
  html, body { width: 1200px; height: 846px; overflow: hidden; }
  body {
    background: var(--page);
    font-family: "Montserrat", sans-serif;
    position: relative;
  }
  .card {
    position: absolute;
    top: 153px;
    width: 310px;
    height: 540px;
    overflow: hidden;
    box-shadow: 0 10px 28px rgba(0,0,0,0.28);
  }
  .card--front { left: 240px; background: var(--card-front); }
  .card--back { left: 650px; background: var(--card-back); }
  .card__texture {
    position: absolute;
    inset: 0;
    background:
      linear-gradient(135deg, var(--texture-light) 0%, transparent 40%),
      linear-gradient(315deg, var(--texture-dark) 0%, transparent 55%);
    opacity: 0.8;
  }
  .card__content {
    position: relative;
    height: 100%;
    display: flex;
    flex-direction: column;
    align-items: center;
  }

  /* Front */
  .brand {
    margin-top: 110px;
    display: flex;
    flex-direction: column;
    align-items: center;
    gap: 10px;
  }
  .brand__mark {
    width: 14px;
    height: 14px;
    background: var(--gold);
  }
  .brand__name {
    color: var(--gold);
    font-weight: 700;
    font-size: 17px;
    letter-spacing: 1.5px;
    text-transform: uppercase;
    text-align: center;
    line-height: 1.35;
  }
  .brand__rule {
    width: 150px;
    height: 1px;
    background: var(--gold-deep);
  }
  .person { margin-top: 38px; text-align: center; }
  .person__name {
    color: var(--gold);
    font-weight: 800;
    font-size: 21px;
    letter-spacing: 0.5px;
  }
  .person__role {
    color: var(--silver);
    font-weight: 500;
    font-size: 13px;
    margin-top: 2px;
    letter-spacing: 0.5px;
  }
  .contact-icons {
    margin-top: 22px;
    position: relative;
    width: 190px;
    display: flex;
    justify-content: space-between;
  }
  .contact-icons::before {
    content: "";
    position: absolute;
    left: -20px; right: -20px; top: 50%;
    height: 1px;
    background: var(--gold-deep);
  }
  .contact-icons__item {
    position: relative;
    width: 30px; height: 30px;
    background: var(--gold);
    display: flex;
    align-items: center;
    justify-content: center;
  }
  .contact-icons__item svg { width: 18px; height: 18px; }
  .phone {
    margin-top: 20px;
    color: var(--gold);
    font-weight: 800;
    font-size: 25px;
    letter-spacing: 1px;
  }
  .web-details {
    margin-top: 6px;
    color: var(--silver);
    font-size: 12.5px;
    line-height: 1.7;
    text-align: center;
    letter-spacing: 0.3px;
  }

  /* Back */
  .card--back .card__content { justify-content: center; }
  .brand--vertical {
    margin: 0;
    transform: rotate(-90deg);
    white-space: nowrap;
    flex-direction: row;
    gap: 12px;
  }
  .brand--vertical .brand__name { font-size: 22px; }
  .brand--vertical .brand__mark { width: 18px; height: 18px; }
</style>
</head>
<body>

  <section class="card card--front" aria-label="Business card front">
    <div class="card__texture" role="img" aria-label="Subtle embossed abstract pattern in dark greys"></div>
    <div class="card__content">
      <div class="brand">
        <span class="brand__mark"></span>
        <p class="brand__name">Renwick Tolliver<br>Construction</p>
        <span class="brand__rule"></span>
      </div>

      <div class="person">
        <h1 class="person__name">Lionel Ashby</h1>
        <p class="person__role">Managing Director</p>
      </div>

      <div class="contact-icons">
        <span class="contact-icons__item" aria-label="Phone">
          <svg viewBox="0 0 24 24"><path fill="#141414" d="M6.6 10.8a15.1 15.1 0 0 0 6.6 6.6l2.2-2.2a1 1 0 0 1 1-.25 11.4 11.4 0 0 0 3.6.57 1 1 0 0 1 1 1V20a1 1 0 0 1-1 1A17 17 0 0 1 3 4a1 1 0 0 1 1-1h3.5a1 1 0 0 1 1 1c0 1.25.2 2.45.57 3.57a1 1 0 0 1-.25 1z"/></svg>
        </span>
        <span class="contact-icons__item" aria-label="Email">
          <svg viewBox="0 0 24 24"><rect x="3" y="6" width="18" height="12" fill="none" stroke="#141414" stroke-width="1.8"/><path d="M3 6l9 7 9-7" fill="none" stroke="#141414" stroke-width="1.8"/></svg>
        </span>
        <span class="contact-icons__item" aria-label="Website">
          <svg viewBox="0 0 24 24" fill="none" stroke="#141414" stroke-width="1.6"><circle cx="12" cy="12" r="8.5"/><ellipse cx="12" cy="12" rx="3.8" ry="8.5"/><path d="M3.5 12h17M5 7.5h14M5 16.5h14"/></svg>
        </span>
      </div>

      <p class="phone">07822 254 961</p>
      <p class="web-details">info@renwick-tolliver.co.uk<br>www.renwick-tolliver.co.uk</p>
    </div>
  </section>

  <section class="card card--back" aria-label="Business card back">
    <div class="card__texture" role="img" aria-label="Subtle embossed abstract pattern in deep greys"></div>
    <div class="card__content">
      <div class="brand brand--vertical">
        <span class="brand__mark"></span>
        <p class="brand__name">Renwick Tolliver Construction</p>
      </div>
    </div>
  </section>

</body>
</html>
```